Gobal construction supply company needs new business card design

I need a business card design for my global supply company using an existing logo. i will be looking to print these on rounded corner cards with the black background version of my logo on the back. on the front white background, my logo again and my simple details.

```html
<!DOCTYPE html>
<html lang="en">
<head>
<meta charset="utf-8">
<title>Harbourline Supply — Business Card</title>
<link rel="stylesheet" href="https://fonts.googleapis.com/css2?family=Roboto:wght@400;500;700&display=swap">
<style>
  :root {
    --backdrop: #8d8b89;
    --card-white: #f4f4f4;
    --card-black: #1c1c1c;
    --brand-red: #d50000;
    --ink: #111111;
    --paper-text: #ffffff;
    --edge-grey: #9c9c9c;
  }
  * { margin: 0; padding: 0; box-sizing: border-box; }
  html, body {
    width: 1200px;
    height: 960px;
    overflow: hidden;
    background: var(--backdrop);
    font-family: "Roboto", Arial, sans-serif;
  }
  .card {
    position: absolute;
    width: 600px;
    height: 343px;
    border-radius: 22px;
    overflow: hidden;
  }
  .card-front { left: 314px; top: 113px; background: var(--card-white); }
  .card-back  { left: 311px; top: 472px; background: var(--card-black); }

  .front-panel { position: absolute; left: 0; top: 0; width: 600px; height: 343px; }

  .brand-mark {
    position: absolute;
    display: flex;
    align-items: center;
    gap: 12px;
    font-weight: 700;
    letter-spacing: 0.5px;
    white-space: nowrap;
  }
  .brand-mark .dot {
    width: 26px; height: 26px;
    border-radius: 50%;
    background: var(--brand-red);
    flex: none;
  }
  .brand-front { right: 37px; top: 70px; font-size: 30px; color: var(--ink); }
  .brand-back {
    left: 0; right: 0; top: 188px;
    justify-content: center;
    font-size: 34px;
    color: var(--paper-text);
  }

  .holder {
    position: absolute;
    right: 69px;
    top: 158px;
    text-align: right;
  }
  .holder-name { font-size: 22px; font-weight: 500; color: var(--ink); line-height: 26px; letter-spacing: 0.3px; }
  .holder-title { font-size: 14.5px; font-weight: 500; color: var(--brand-red); line-height: 18px; }

  .contact {
    position: absolute;
    left: 43px;
    top: 181px;
    color: var(--paper-text);
    font-size: 14.5px;
    line-height: 18px;
  }
  .address { margin-bottom: 12px; }
  .contact-list { list-style: none; }
  .contact-list li { display: flex; align-items: center; height: 19px; }
  .contact-list svg { width: 13px; height: 13px; margin-right: 10px; fill: var(--paper-text); flex: none; }
</style>
</head>
<body>

<section class="card card-front">
  <svg class="front-panel" viewBox="0 0 600 343" aria-hidden="true">
    <polyline points="0,161 275,161 397,343" fill="none" stroke="var(--edge-grey)" stroke-width="3"/>
    <polygon points="0,163 273,163 395,343 0,343" fill="var(--brand-red)"/>
  </svg>

  <div class="brand-mark brand-front"><span>HARBOURLINE</span><span class="dot"></span></div>

  <div class="holder">
    <p class="holder-name">DANIEL HARPER</p>
    <p class="holder-title">CEO/FOUNDER</p>
  </div>

  <div class="contact">
    <p class="address">4120 Ridgewood Drive<br>Fairbanks, Alaska 99701</p>
    <ul class="contact-list">
      <li><svg viewBox="0 0 16 16"><path d="M3.5 1l2.5 3-1.5 2c.8 2 2.5 3.7 4.5 4.5l2-1.5 3 2.5-1.5 2.5C7 15 1 9 1 2.5z"/></svg>555 210 4871</li>
      <li><svg viewBox="0 0 16 16"><path d="M4 0h8v16H4zM5.5 2v10h5V2zM7 13.5h2v1H7z" fill-rule="evenodd"/></svg>555 382 6190</li>
      <li><svg viewBox="0 0 16 16"><path d="M4 1h8v4H4zM1 6h14v6h-2v3H3v-3H1zM4.5 10v3.5h7V10z" fill-rule="evenodd"/></svg>555 734 2056</li>
      <li><svg viewBox="0 0 16 16"><path d="M1 3h14v10H1zM2.5 4.5L8 9l5.5-4.5v-0.2h-11z" fill-rule="evenodd"/></svg>daniel@harbourlinesupply.com</li>
      <li><svg viewBox="0 0 16 16"><path d="M8 1a7 7 0 1 0 0 14A7 7 0 0 0 8 1zm-1 2.5c-1 .8-2.5 1-3 2.5l2 1.5 1 2-1 2.5 1.5 1c.5-1.5 2-2 2-3.5l-2-1.5 1-2 2.5.5-.5-2.5z" fill-rule="evenodd"/></svg>www.harbourlinesupply.com</li>
    </ul>
  </div>
</section>

<section class="card card-back">
  <div class="brand-mark brand-back"><span>HARBOURLINE SUPPLY</span><span class="dot"></span></div>
</section>

</body>
</html>
```